Shop front signage design for Bubble Tea Shop

Pearl Hollow is Sydney based Green Tea Shop.We are looking for a modern and sleek signage for shop front end. We have Aluminium Composite Panel and Awning sign at the shop front. We will keep Aluminium composite panel simple with logo and text. We are after awning design which is above glass door and under the panel. Old Awning is PVC foam in two pieces 2310mm w x 1000mm h. We need someone to design awing. It should reflect Bubble tea and using bubble tea cups with pearls is essential. Stock images can be used. Avoid using icons or illustrative icons as we are after real images of bubble tea cup. This is to ensure that the brand is not taken as juice shop or cafe.
Panel Dimensions is 5250 mm w x 580 mm h.Awning/ Fascia sign is 4720 mm w x 1000 mm h.
Logo and signage concept is attached.

Target Market(s)

Corporate Male and Female, school, general public.

Colors
f36e22
333333
000000
eaeaea
cbcbcb

Requirements
Must have
• Bubble tea cups with fruit or milk tea.
Should not have
• Icons, illustration

```html
<!DOCTYPE html>
<html lang="en">
<head>
<meta charset="utf-8">
<title>Pearl Hollow – Awning Sign</title>
<link href="https://fonts.googleapis.com/css2?family=Poppins:wght@700&display=swap" rel="stylesheet">
<style>
  :root {
    --page-bg: #eaeaea;
    --sign-white: #ffffff;
    --panel-top: #ffffff;
    --panel-bottom: #cbcbcb;
    --ink: #000000;
    --ink-soft: #333333;
    --cup-purple: #a98bc4;
    --cup-pink: #f2b7c4;
    --cup-yellow: #dcd56a;
  }
  html, body {
    margin: 0;
    width: 1200px;
    height: 1000px;
    overflow: hidden;
    background: var(--page-bg);
  }
  .canvas {
    position: relative;
    width: 1200px;
    height: 1000px;
  }
  .awning {
    position: absolute;
    left: 0;
    top: 0;
    width: 1200px;
    height: 1000px;
  }
  .brand-name {
    font-family: "Poppins", sans-serif;
    font-weight: 700;
    font-size: 53px;
    letter-spacing: -0.5px;
    fill: var(--ink);
  }
</style>
</head>
<body>
<div class="canvas">
  <svg class="awning" viewBox="0 0 1200 1000" xmlns="http://www.w3.org/2000/svg">
    <defs>
      <linearGradient id="panelShade" x1="0" y1="0" x2="0" y2="1">
        <stop offset="0" stop-color="var(--panel-top)"/>
        <stop offset="1" stop-color="var(--panel-bottom)"/>
      </linearGradient>
      <linearGradient id="cupTones" x1="0" y1="0" x2="1" y2="0">
        <stop offset="0" stop-color="var(--cup-purple)"/>
        <stop offset="0.5" stop-color="var(--cup-pink)"/>
        <stop offset="1" stop-color="var(--cup-yellow)"/>
      </linearGradient>
    </defs>

    <rect class="sign-board" x="52" y="417" width="1080" height="230" fill="var(--sign-white)"/>

    <polygon class="centre-panel" points="278,417 905,417 820,647 365,647" fill="url(#panelShade)"/>

    <g class="rule-left" stroke="var(--ink)" stroke-width="2">
      <line x1="264" y1="417" x2="351" y2="647"/>
      <line x1="271" y1="417" x2="358" y2="647"/>
      <line x1="278" y1="417" x2="365" y2="647"/>
    </g>

    <g class="rule-right" stroke="var(--ink)" stroke-width="2">
      <line x1="919" y1="417" x2="834" y2="647"/>
      <line x1="912" y1="417" x2="827" y2="647"/>
      <line x1="905" y1="417" x2="820" y2="647"/>
    </g>

    <rect class="cup-photo cup-photo-left" x="98" y="432" width="172" height="198" rx="14"
          fill="url(#cupTones)" role="img"
          aria-label="Photo of three bubble tea cups with straws: taro, strawberry milk and mango, with tapioca pearls"/>
    <rect class="cup-photo cup-photo-right" x="906" y="432" width="172" height="198" rx="14"
          fill="url(#cupTones)" role="img"
          aria-label="Photo of three bubble tea cups with straws: taro, strawberry milk and mango, with tapioca pearls"/>

    <circle class="brand-dot" cx="421" cy="557" r="44" fill="none" stroke="var(--ink)" stroke-width="6"/>
    <text class="brand-name" x="483" y="580" textLength="327" lengthAdjust="spacingAndGlyphs">Pearl Hollow</text>
  </svg>
</div>
</body>
</html>
```